Satchel & Sundial needs new business card design

I need a new business card design. I'm looking for out-of-the-box design which represents the freedom of being a location independent entrepreneur.
I offer coaching, retreats and trips.
I would like to see designs with and without the photo.
Colors I use are black (#000000), green (#25A796) and brown (#D7C38C)
Website satchelandsundial.example

Target Market(s)

location independent entrepreneurs, digital nomads, people looking to swap the 9 to 5 for a lifestyle business

Industry/Entity Type

Business

Contact Information for Business Card

Dorota Falkner
Your Lifestyle Business Coach, Retreat & Trip Leader
http://satchelandsundial.example
hello@satchelandsundial.example
Live a life you don't need a holiday from

Font styles to use
Serif
Sans Serif

Requirements
Must have
• One side should contain only the logo. I would also consider having the "Live a life you don't need a holiday from" on that side too (depending on how it looks)
• Please show both sides on the designs.

```html
<!DOCTYPE html>
<html lang="en">
<head>
<meta charset="utf-8">
<title>Satchel &amp; Sundial – Business Card</title>
<link rel="stylesheet" href="https://fonts.googleapis.com/css2?family=Open+Sans:wght@400;600;700&display=swap">
<style>
  :root {
    --stage: #2b2b2b;
    --card-dark: #231f20;
    --brand-green: #25a796;
    --card-green: #22a998;
    --ink-white: #ffffff;
    --ink-dark: #231f20;
  }
  * { box-sizing: border-box; margin: 0; padding: 0; }
  html, body {
    width: 1200px; height: 900px; overflow: hidden;
    background: var(--stage);
    font-family: "Open Sans", Arial, sans-serif;
  }
  .stage {
    width: 1200px; height: 900px;
    display: flex; align-items: center; justify-content: center; gap: 60px;
  }
  .card {
    position: relative;
    width: 525px; height: 300px;
    border-radius: 26px;
    box-shadow: 0 14px 30px rgba(0,0,0,.45);
  }
  .card--contact { background: var(--card-dark); color: var(--ink-white); }
  .card--logo { background: var(--card-green); }

  .contact-lines {
    position: absolute; top: 34px; right: 30px;
    text-align: right; font-size: 13px; line-height: 19px;
  }
  .contact-line { display: flex; align-items: center; justify-content: flex-end; gap: 7px; }
  .contact-icon { width: 11px; height: 11px; flex: none; }

  .person { position: absolute; top: 112px; left: 34px; }
  .person-name { color: var(--brand-green); font-weight: 700; font-size: 17px; line-height: 22px; }
  .person-role { font-size: 13.5px; line-height: 19px; }

  .brand-name {
    font-weight: 700; font-size: 34px; letter-spacing: 1px;
    text-transform: uppercase; white-space: nowrap;
  }
  .card--contact .brand-name {
    position: absolute; top: 168px; left: 0; right: 0; text-align: center;
    color: var(--ink-white);
  }
  .tagline {
    position: absolute; left: 34px; bottom: 28px;
    font-size: 11.5px; font-weight: 600; text-transform: uppercase; letter-spacing: .2px;
  }

  .card--logo .brand-name {
    position: absolute; top: 104px; left: 0; right: 0; text-align: center;
    color: var(--ink-dark);
  }
  .services {
    position: absolute; top: 192px; left: 0; right: 0; text-align: center;
    color: var(--ink-white); font-weight: 600; font-size: 15px;
  }
</style>
</head>
<body>
<main class="stage">
  <section class="card card--contact" aria-label="Card back with contact details">
    <div class="contact-lines">
      <p class="contact-line">hello@satchelandsundial.example
        <svg class="contact-icon" viewBox="0 0 11 11" aria-hidden="true"><rect x="0" y="2" width="11" height="7.5" rx="1" fill="var(--brand-green)"/><path d="M0.5 2.5 L5.5 6 L10.5 2.5" stroke="var(--card-dark)" stroke-width="1" fill="none"/></svg>
      </p>
      <p class="contact-line">www.satchelandsundial.example
        <svg class="contact-icon" viewBox="0 0 11 11" aria-hidden="true"><circle cx="5.5" cy="5.5" r="5.2" fill="var(--brand-green)"/><path d="M5.5 0.5 V10.5 M0.5 5.5 H10.5" stroke="var(--card-dark)" stroke-width=".8"/></svg>
      </p>
    </div>
    <div class="person">
      <p class="person-name">Dorota Falkner</p>
      <p class="person-role">Your Lifestyle Business Coach</p>
      <p class="person-role">Retreat &amp; Trip Leader</p>
    </div>
    <p class="brand-name">Satchel &amp; Sundial</p>
    <p class="tagline">Live a life you don't need a holiday from</p>
  </section>

  <section class="card card--logo" aria-label="Card front with brand name">
    <p class="brand-name">Satchel &amp; Sundial</p>
    <p class="services">Coaching | Retreats | Trips</p>
  </section>
</main>
</body>
</html>
```